New business Cards

We need some new cards that stand out. We love our logo and colour scheme but need to incorporate a quorva logo and tlm logo yet still keep our cards uncluttered and clean looking.
Our tag is Brisk Ledgerworks. Anywhere, Anytime.
The idea of the cards is to show authority in accounting and Quorva/ cloud software

Industry/Entity Type

Business

```html
<!DOCTYPE html>
<html lang="en">
<head>
<meta charset="utf-8">
<title>Halden Business Solutions – Business Cards</title>
<link rel="stylesheet" href="https://fonts.googleapis.com/css2?family=Open+Sans:wght@400;600&display=swap">
<style>
  :root {
    --bg: #e9e6e1;
    --card-black: #111111;
    --card-black-soft: #242424;
    --card-white: #ffffff;
    --brand-green: #6cb33f;
    --text-light: #e6e6e6;
    --text-dark: #2b2b2b;
    --badge-blue: #2c4a9a;
    --badge-teal: #1fb6d4;
    --badge-teal-dark: #0f8aa3;
  }
  * { box-sizing: border-box; margin: 0; padding: 0; }
  html, body {
    width: 1200px; height: 1024px; overflow: hidden;
    background: var(--bg);
    font-family: "Open Sans", Arial, sans-serif;
  }
  .canvas { position: relative; width: 1200px; height: 1024px; }

  .card {
    position: absolute; left: 220px; width: 760px; height: 430px;
    border-radius: 4px; overflow: hidden;
    box-shadow: 0 14px 30px rgba(0,0,0,.25);
  }
  .card--front { top: 58px; background: var(--card-white); }
  .card--back  { top: 536px; background: linear-gradient(160deg, var(--card-black-soft), var(--card-black) 55%); }

  /* Front */
  .front__upper { position: absolute; left: 0; top: 0; width: 100%; height: 235px; background: var(--card-white); }
  .front__lower {
    position: absolute; left: 0; top: 235px; width: 100%; height: 195px;
    background: linear-gradient(180deg, var(--card-black-soft), var(--card-black));
  }
  .front__accent { position: absolute; left: 0; top: 235px; width: 100%; height: 4px; background: var(--brand-green); }

  .brand { position: absolute; display: flex; align-items: center; gap: 12px; color: var(--brand-green); font-weight: 600; }
  .brand__square { width: 54px; height: 54px; background: var(--brand-green); }
  .brand__name { font-size: 34px; letter-spacing: 4px; line-height: 1; text-transform: uppercase; }
  .brand__sub { font-size: 14px; letter-spacing: 2.5px; line-height: 1.4; text-transform: lowercase; }
  .front .brand { left: 44px; top: 78px; }

  .partners { position: absolute; right: 46px; top: 40px; display: flex; align-items: center; gap: 14px; }
  .partner-mark { display: flex; align-items: center; gap: 6px; color: var(--badge-teal-dark); font-weight: 600; font-size: 15px; }
  .partner-mark__dot { width: 30px; height: 30px; border-radius: 50%; background: var(--badge-teal); }
  .partner-badge { width: 30px; height: 30px; border-radius: 50%; background: var(--badge-teal-dark); }
  .partner-tlm { display: flex; align-items: center; gap: 6px; color: var(--badge-blue); font-weight: 600; font-size: 18px; text-transform: uppercase; }
  .partner-tlm__square { width: 58px; height: 58px; background: var(--badge-blue); }

  .contact { position: absolute; left: 44px; top: 286px; list-style: none; color: var(--text-light); font-size: 17px; line-height: 30px; }
  .contact li { display: flex; align-items: center; gap: 10px; }
  .contact svg { width: 16px; height: 16px; fill: var(--brand-green); }

  .person { position: absolute; right: 46px; top: 268px; text-align: right; color: var(--text-light); font-size: 17px; line-height: 28px; }
  .person__name { color: var(--brand-green); font-size: 19px; font-weight: 600; }
  .person__web { margin-top: 10px; }

  /* Back */
  .back__rule { position: absolute; left: 0; top: 92px; width: 100%; height: 2px; background: var(--brand-green); }
  .back__tagline { position: absolute; left: 44px; top: 108px; color: var(--text-light); font-size: 24px; letter-spacing: 1px; text-transform: uppercase; }
  .back__web { position: absolute; left: 44px; top: 148px; color: var(--brand-green); font-size: 17px; letter-spacing: .5px; }
  .back__band { position: absolute; left: 0; top: 200px; width: 100%; height: 130px; background: linear-gradient(180deg, rgba(255,255,255,.05), rgba(255,255,255,0)); }
  .back .brand { left: 400px; top: 230px; color: var(--brand-green); }
  .back .brand__square { width: 72px; height: 72px; }
  .back .brand__name { font-size: 40px; }
</style>
</head>
<body>
<main class="canvas">

  <section class="card card--front front" aria-label="Business card front">
    <div class="front__upper"></div>
    <div class="front__lower"></div>
    <div class="front__accent"></div>

    <div class="brand">
      <span class="brand__square"></span>
      <div>
        <div class="brand__name">Halden</div>
        <div class="brand__sub">business solutions</div>
      </div>
    </div>

    <div class="partners">
      <div class="partner-mark"><span class="partner-mark__dot"></span>quorva</div>
      <span class="partner-badge" aria-label="Partner badge"></span>
      <div class="partner-tlm"><span class="partner-tlm__square"></span>tlm</div>
    </div>

    <ul class="contact">
      <li>
        <svg viewBox="0 0 16 16"><path d="M8 0a5.5 5.5 0 0 0-5.5 5.5C2.5 10 8 16 8 16s5.5-6 5.5-10.5A5.5 5.5 0 0 0 8 0zm0 8a2.5 2.5 0 1 1 0-5 2.5 2.5 0 0 1 0 5z"/></svg>
        Bexley Vic 3190
      </li>
      <li>
        <svg viewBox="0 0 16 16"><path d="M3.5 1l2.5 3-1.5 2a9 9 0 0 0 5 5l2-1.5 3 2.5-1.5 2.5C7 15 1 9 1 2.5z"/></svg>
        03 5550 1298
      </li>
      <li>
        <svg viewBox="0 0 16 16"><path d="M0 3h16v10H0zm1.5 1.2V5l6.5 4 6.5-4v-.8z"/></svg>
        maren@haldenbiz.com.au
      </li>
    </ul>

    <div class="person">
      <div class="person__name">Maren Tolley, TLM, CTA</div>
      <div class="person__role">Partner</div>
      <div class="person__web">www.haldenbiz.com.au</div>
    </div>
  </section>

  <section class="card card--back back" aria-label="Business card back">
    <div class="back__rule"></div>
    <p class="back__tagline">Brisk Ledgerworks. Anywhere, Anytime.</p>
    <p class="back__web">www.haldenbiz.com.au</p>
    <div class="back__band"></div>
    <div class="brand">
      <span class="brand__square"></span>
      <div>
        <div class="brand__name">Halden</div>
        <div class="brand__sub">business solutions</div>
      </div>
    </div>
  </section>

</main>
</body>
</html>
```